Business Card: RW Office Partners - Your organised problem solver

Business Name: RW Office Partners
Website: www.rwofficepartners.com.au
Email: marisol@rwofficepartners.com.au
Mobile: 61 482 907 236
Facebook: @rwofficepartners
Instrgram: @rwofficepartners

Brading Colours:
HEX
#986474
#ddccd3
#7a8498
#c9d8e4
#000000
#ffffff

Tag Line: Your organised problem solver

Link to DRAFT website:
https://deskhelpcollective.wixsite.com/rw-office-partners

About Page from the website:
My name is Marisol Wrenfield, and I would love to assist you to become more productive in your day to day and achieve your business and personal goals.
My mission is to give you time, time to work on the important tasks of your business or to be able to spend more time with your family. I will take on the tasks you don’t have time for, don’t know well or simply don’t like to do.
I have an extensive background in Administration, Tender Coordination, Document Control, WHS and Quality Management working primarily in the Construction, Mining and Corporate World.
I am passionate about being organised, having order and making things in your life (and mine) easier! I love to watch something unfold and grow into something amazing! I am known for being the go-to problem solver, the organiser of all things, producing high standards of work even under pressure. I’m also a confident communicator, and I understand that you’re busy running your business.

Target Market(s)

Small to Medium Business who require assistance in their business by a virtual assistant.

Industry/Entity Type

Virtual Assistant

Contact Information for Business Card

Mobile: 61 482 907 236

Font styles to use
Sans Serif

Colors
ffffff

Requirements
Must have
• Branding Colours as outlined.
Contact Details as outlined.
Logo as provided.
Proper contact details - mobile, facebook, instragm, website.
Simple, Elegant, very clean looking.
Should not have
• Note cute with pictures.
Not too girly as still want to market to construction companies.

```html
<!DOCTYPE html>
<html lang="en">
<head>
<meta charset="utf-8">
<title>RW Office Partners – Business Card</title>
<link rel="stylesheet" href="https://fonts.googleapis.com/css2?family=Roboto:wght@400;500&display=swap">
<style>
  :root {
    --mauve: #986474;
    --mauve-deep: #84505f;
    --blush: #ddccd3;
    --slate: #7a8498;
    --mist: #c9d8e4;
    --ink: #000000;
    --paper: #ffffff;
    --backdrop: #ecebee;
  }
  * { margin: 0; padding: 0; box-sizing: border-box; }
  html, body {
    width: 1200px;
    height: 1054px;
    overflow: hidden;
    background: var(--backdrop);
    font-family: "Roboto", Arial, sans-serif;
  }
  .card {
    position: absolute;
    left: 100px;
    top: 227px;
    width: 1000px;
    height: 600px;
    border-radius: 26px;
    overflow: hidden;
    box-shadow: 0 10px 30px rgba(0,0,0,0.12);
  }
  .card-shapes {
    position: absolute;
    inset: 0;
  }
  .brand-name {
    position: absolute;
    left: 40px;
    top: 232px;
    width: 330px;
    text-align: center;
    color: var(--mauve);
    font-weight: 500;
    font-size: 46px;
    line-height: 1.12;
    letter-spacing: 0.5px;
  }
  .identity {
    position: absolute;
    left: 489px;
    top: 118px;
    color: var(--blush);
  }
  .person-name {
    font-weight: 500;
    font-size: 37px;
    line-height: 1.1;
  }
  .person-role {
    font-weight: 400;
    font-size: 25px;
    margin-top: 6px;
  }
  .contact-list {
    position: absolute;
    left: 489px;
    top: 238px;
    list-style: none;
    color: var(--blush);
    font-size: 25px;
  }
  .contact-item {
    display: flex;
    align-items: center;
    height: 38.3px;
  }
  .contact-icon {
    width: 24px;
    height: 24px;
    margin-right: 19px;
    flex: none;
  }
  .tagline-band {
    position: absolute;
    left: 380px;
    right: 0;
    top: 499px;
    height: 50px;
    background: rgba(201,216,228,0.22);
    display: flex;
    align-items: center;
    padding-left: 109px;
    color: var(--blush);
    font-size: 24px;
  }
</style>
</head>
<body>
  <div class="card">
    <svg class="card-shapes" width="1000" height="600" viewBox="0 0 1000 600" aria-hidden="true">
      <rect width="1000" height="600" fill="var(--mauve)"/>
      <path d="M0 0 H392 Q458 300 373 600 H0 Z" fill="var(--slate)"/>
      <path d="M0 0 H376 Q442 300 357 600 H0 Z" fill="var(--paper)"/>
    </svg>

    <div class="brand-name">RW Office<br>Partners</div>

    <div class="identity">
      <div class="person-name">Marisol Wrenfield</div>
      <div class="person-role">Virtual Assistant</div>
    </div>

    <ul class="contact-list">
      <li class="contact-item">
        <svg class="contact-icon" viewBox="0 0 24 24" aria-hidden="true">
          <path d="M3 9 Q12 2 21 9 L19 11 L16 9 V7.5 Q12 6 8 7.5 V9 L5 11 Z" fill="var(--blush)"/>
          <path d="M7 11 H17 L20 19 H4 Z" fill="var(--blush)"/>
          <circle cx="12" cy="15" r="2.2" fill="var(--mauve)"/>
        </svg>
        61 482 907 236
      </li>
      <li class="contact-item">
        <svg class="contact-icon" viewBox="0 0 24 24" aria-hidden="true">
          <rect x="2" y="5" width="20" height="14" fill="var(--blush)"/>
          <path d="M2 5 L12 13 L22 5 M2 19 L9.5 11 M22 19 L14.5 11" stroke="var(--mauve)" stroke-width="1.6" fill="none"/>
        </svg>
        marisol@rwofficepartners.com.au
      </li>
      <li class="contact-item">
        <svg class="contact-icon" viewBox="0 0 24 24" aria-hidden="true">
          <g fill="none" stroke="var(--blush)" stroke-width="1.8">
            <circle cx="12" cy="12" r="9"/>
            <ellipse cx="12" cy="12" rx="4" ry="9"/>
            <path d="M3 12 H21"/>
          </g>
        </svg>
        www.rwofficepartners.com.au
      </li>
      <li class="contact-item">
        <svg class="contact-icon" viewBox="0 0 24 24" aria-hidden="true">
          <rect x="2" y="2" width="20" height="20" rx="3" fill="var(--blush)"/>
        </svg>
        @rwofficepartners
      </li>
      <li class="contact-item">
        <svg class="contact-icon" viewBox="0 0 24 24" aria-hidden="true">
          <circle cx="12" cy="12" r="10" fill="var(--blush)"/>
        </svg>
        @rwofficepartners
      </li>
    </ul>

    <div class="tagline-band">Your organised problem solver</div>
  </div>
</body>
</html>
```